Business Card for Coastal Tundrabridge Advisory

We need a business card for Coastal Tundrabridge Advisory. The company website address is provided below. The company logo is attached. We provide specialized permafrost services to the mining, transportation, and oil & gas industries. The card should be prepared for:
Matthias Korhonen, PhD.
Coastal Tundrabridge Advisory
PO Box 418259
Quillwater, Alaska 99642
Direct: +1-907-555-0143
Email: mkorhonen@tundrabridgeadvisory.example
Website: www.coastaltundrabridgeadvisory.example

```html
<!DOCTYPE html>
<html lang="en">
<head>
<meta charset="utf-8">
<title>Coastal Tundrabridge Advisory – Business Card</title>
<link href="https://fonts.googleapis.com/css2?family=Roboto:wght@300;400;500;700&display=swap" rel="stylesheet">
<style>
  :root {
    --backdrop: #232323;
    --card: #111722;
    --ink: #ffffff;
    --ink-soft: #d9dde4;
    --rule: #8a909a;
  }
  * { margin: 0; padding: 0; box-sizing: border-box; }
  html, body {
    width: 1200px; height: 711px; overflow: hidden;
    background: var(--backdrop);
    font-family: "Roboto", Arial, sans-serif;
    color: var(--ink);
  }
  .stage {
    width: 1200px; height: 711px;
    display: flex; align-items: center; justify-content: center; gap: 40px;
  }
  .card {
    position: relative;
    width: 560px; height: 320px;
    background: var(--card);
    overflow: hidden;
  }
  .edge-bar {
    position: absolute; width: 10px; height: 150px; background: var(--ink);
  }
  .edge-bar--left { left: 0; top: 150px; }
  .edge-bar--right { right: 0; top: 22px; }

  .wordmark {
    font-weight: 500; text-transform: uppercase; letter-spacing: 3px;
    line-height: 1.25; color: var(--ink);
  }
  .card--front .wordmark {
    position: absolute; left: 0; right: 0; top: 118px;
    text-align: center; font-size: 28px;
  }
  .card--back .wordmark {
    position: absolute; left: 42px; top: 152px;
    font-size: 15px; letter-spacing: 2px;
  }
  .divider {
    position: absolute; left: 290px; top: 70px;
    width: 1px; height: 160px; background: var(--rule);
  }
  .identity { position: absolute; left: 312px; top: 78px; }
  .identity__name { font-size: 23px; font-weight: 700; line-height: 1.1; }
  .identity__surname { font-weight: 300; }
  .identity__title { font-size: 13px; font-weight: 700; margin: 3px 0 0 12px; }
  .contacts {
    position: absolute; left: 322px; top: 160px;
    list-style: none; font-size: 9.5px; color: var(--ink-soft);
  }
  .contacts__item { display: flex; align-items: center; gap: 6px; height: 17px; }
  .contacts__icon { width: 10px; height: 10px; fill: var(--ink); flex: none; }
  .address {
    position: absolute; left: 0; right: 0; top: 270px;
    text-align: center; font-size: 11px; color: var(--ink-soft);
  }
</style>
</head>
<body>
<main class="stage">
  <section class="card card--front" aria-label="Card front">
    <span class="edge-bar edge-bar--left"></span>
    <span class="edge-bar edge-bar--right"></span>
    <p class="wordmark">Coastal Tundrabridge<br>Advisory</p>
  </section>

  <section class="card card--back" aria-label="Card back">
    <span class="edge-bar edge-bar--left"></span>
    <span class="edge-bar edge-bar--right"></span>
    <p class="wordmark">Coastal Tundrabridge<br>Advisory</p>
    <span class="divider"></span>
    <div class="identity">
      <p class="identity__name">Matthias <span class="identity__surname">Korhonen</span></p>
      <p class="identity__title">PhD</p>
    </div>
    <ul class="contacts">
      <li class="contacts__item">
        <svg class="contacts__icon" viewBox="0 0 24 24" aria-hidden="true"><path d="M6.6 10.8a15.1 15.1 0 0 0 6.6 6.6l2.2-2.2c.3-.3.7-.4 1-.2 1.1.4 2.3.6 3.6.6.6 0 1 .4 1 1V20c0 .6-.4 1-1 1A17 17 0 0 1 3 4c0-.6.4-1 1-1h3.5c.6 0 1 .4 1 1 0 1.3.2 2.5.6 3.6.1.3 0 .7-.2 1z"/></svg>
        <span>+1-907-555-0143</span>
      </li>
      <li class="contacts__item">
        <svg class="contacts__icon" viewBox="0 0 24 24" aria-hidden="true"><path d="M2 5h20v14H2zm2 2v.4l8 5.2 8-5.2V7zm0 2.8V17h16V9.8l-8 5.2z"/></svg>
        <span>mkorhonen@tundrabridgeadvisory.example</span>
      </li>
      <li class="contacts__item">
        <svg class="contacts__icon" viewBox="0 0 24 24" aria-hidden="true"><path d="M12 2a10 10 0 1 0 0 20 10 10 0 0 0 0-20zm6.9 6h-3a15 15 0 0 0-1.3-3.9A8 8 0 0 1 18.9 8zM12 4c.8 1.2 1.5 2.5 1.9 4h-3.8c.4-1.5 1.1-2.8 1.9-4zM4.3 14a8 8 0 0 1 0-4h3.4a16 16 0 0 0 0 4zm.8 2h3a15 15 0 0 0 1.3 3.9A8 8 0 0 1 5.1 16zm3-8h-3a8 8 0 0 1 4.3-3.9A15 15 0 0 0 8.1 8zM12 20c-.8-1.2-1.5-2.5-1.9-4h3.8c-.4 1.5-1.1 2.8-1.9 4zm2.3-6H9.7a14 14 0 0 1 0-4h4.6a14 14 0 0 1 0 4zm.3 5.9a15 15 0 0 0 1.3-3.9h3a8 8 0 0 1-4.3 3.9zm1.7-5.9a16 16 0 0 0 0-4h3.4a8 8 0 0 1 0 4z"/></svg>
        <span>www.coastaltundrabridgeadvisory.example</span>
      </li>
    </ul>
    <p class="address">PO Box 418259 Quillwater, Alaska 99642</p>
  </section>
</main>
</body>
</html>
```